Business Card Design for Property Development Company Director

I am looking for a professional and unforgettable business card design for our Director of our Property Development Company.
Please see attached .pptx file to find out what information to include. You don't have to follow the exact format shown in the file - I am interested to see your creative flair using the information provided.

```html
<!DOCTYPE html>
<html lang="en">
<head>
<meta charset="utf-8">
<title>Harwell Property Group – Business Card</title>
<link href="https://fonts.googleapis.com/css2?family=Montserrat:wght@400;500;600;700&display=swap" rel="stylesheet">
<style>
  :root {
    --backdrop: #111214;
    --card: #1d1e20;
    --card-edge: #2a2b2e;
    --ink: #f2f2f2;
    --ink-soft: #d6d6d6;
    --accent: #1f66c1;
  }
  * { box-sizing: border-box; margin: 0; padding: 0; }
  html, body { width: 1200px; height: 900px; overflow: hidden; }
  body {
    background: var(--backdrop);
    font-family: "Montserrat", sans-serif;
    color: var(--ink);
    display: flex;
    flex-direction: column;
    align-items: center;
    justify-content: center;
    gap: 40px;
  }
  .card {
    position: relative;
    width: 660px;
    height: 377px;
    background: linear-gradient(135deg, var(--card) 0%, #232427 60%, #1a1b1d 100%);
    border: 1px solid var(--card-edge);
    box-shadow: 0 14px 30px rgba(0,0,0,0.55);
  }
  .brand {
    display: flex;
    align-items: center;
    gap: 12px;
    font-weight: 700;
    font-size: 24px;
    letter-spacing: 1px;
    color: var(--ink);
    white-space: nowrap;
  }
  .brand-mark {
    width: 34px;
    height: 34px;
    background: var(--accent);
    flex: none;
  }

  /* Front */
  .card-front { display: flex; flex-direction: column; align-items: center; }
  .front-tagline {
    margin-top: 52px;
    text-align: center;
    font-size: 17px;
    line-height: 1.35;
    letter-spacing: 1px;
    color: var(--ink);
  }
  .card-front .brand { margin-top: 62px; }
  .front-invite {
    position: absolute;
    bottom: 40px;
    left: 0; right: 0;
    text-align: center;
    font-size: 16px;
    font-weight: 500;
    letter-spacing: 0.8px;
  }
  .front-invite .highlight { color: var(--accent); }

  /* Back */
  .card-back .brand {
    position: absolute;
    left: 40px;
    top: 118px;
    font-size: 22px;
    line-height: 1.2;
    gap: 12px;
  }
  .card-back .brand-name { display: flex; flex-direction: column; }
  .card-back .brand-mark { width: 40px; height: 40px; }
  .divider {
    position: absolute;
    left: 352px;
    top: 60px;
    width: 2px;
    height: 200px;
    background: var(--accent);
  }
  .contact {
    position: absolute;
    left: 378px;
    top: 58px;
    font-size: 15px;
    color: var(--ink);
  }
  .contact-name {
    color: var(--accent);
    font-size: 23px;
    font-weight: 600;
    letter-spacing: 0.5px;
    text-transform: uppercase;
  }
  .contact-role { font-size: 16px; margin-bottom: 18px; }
  .contact-address { line-height: 1.4; margin-bottom: 14px; }
  .contact-list { list-style: none; line-height: 1.5; }
  .contact-list li { display: flex; align-items: center; gap: 8px; }
  .contact-list svg { width: 12px; height: 12px; flex: none; }
  .licence {
    position: absolute;
    left: 110px;
    bottom: 36px;
    font-size: 18px;
    letter-spacing: 0.5px;
  }
  .licence .label { color: var(--accent); font-weight: 500; }
</style>
</head>
<body>

<section class="card card-front">
  <p class="front-tagline">Property Development<br>&amp; Site Acquisition Specialists</p>
  <div class="brand"><span class="brand-mark"></span>HARWELL PROPERTY GROUP</div>
  <p class="front-invite">Ask me about our <span class="highlight">INVESTMENT &amp; PARTNERSHIP</span> opportunities</p>
</section>

<section class="card card-back">
  <div class="brand"><span class="brand-mark"></span><span class="brand-name"><span>HARWELL</span><span>PROPERTY GROUP</span></span></div>
  <span class="divider"></span>
  <div class="contact">
    <p class="contact-name">Daniel Morrow</p>
    <p class="contact-role">Director</p>
    <p class="contact-address">42 Latham St,<br>Fitzroy VIC 3065, Australia</p>
    <ul class="contact-list">
      <li>
        <svg viewBox="0 0 12 12" aria-hidden="true"><path d="M3 1 L5 3.5 L4 4.8 Q5.2 7 7.2 8 L8.5 7 L11 9 L9.8 11 Q5 10.5 1 3 Z" fill="var(--accent)"/></svg>
        0412 345 678
      </li>
      <li>
        <svg viewBox="0 0 12 12" aria-hidden="true"><rect x="1" y="2.5" width="10" height="7" fill="none" stroke="var(--accent)" stroke-width="1.2"/><path d="M1 2.5 L6 6.5 L11 2.5" fill="none" stroke="var(--accent)" stroke-width="1.2"/></svg>
        daniel@harwellgroup.com.au
      </li>
      <li>
        <svg viewBox="0 0 12 12" aria-hidden="true"><circle cx="6" cy="6" r="5" fill="none" stroke="var(--accent)" stroke-width="1.1"/><ellipse cx="6" cy="6" rx="2.2" ry="5" fill="none" stroke="var(--accent)" stroke-width="1"/><path d="M1 6 H11" stroke="var(--accent)" stroke-width="1"/></svg>
        www.harwellgroup.com.au
      </li>
    </ul>
  </div>
  <p class="licence"><span class="label">Real Estate Lic</span>: 5102394 &amp; 5102395</p>
</section>

</body>
</html>
```